Lumavento business card

We need a modern business card - With our 4 colors - See web: www.lumavento.dk

I have attached logo and som old business Cards we have - Lets Make the new ones shine...:-) -

Industry/Entity Type

Business

Requirements
Must have
• the logo with lumavento only,

```html
<!DOCTYPE html>
<html lang="da">
<head>
<meta charset="utf-8">
<title>Lumavento – visitkort</title>
<link rel="stylesheet" href="https://fonts.googleapis.com/css2?family=Arimo:wght@400;700&display=swap">
<style>
  :root {
    --page-bg: #e6e6e4;
    --brand-green: #8cc63f;
    --card-white: #ffffff;
    --text-grey: #555555;
    --rule-grey: #b5b5b5;
    --card-shadow: rgba(0, 0, 0, 0.18);
  }
  * { box-sizing: border-box; margin: 0; padding: 0; }
  html, body {
    width: 1200px; height: 950px; overflow: hidden;
    background: var(--page-bg);
    font-family: "Arimo", Arial, sans-serif;
  }
  .card {
    position: absolute;
    left: 250px;
    width: 700px; height: 400px;
    box-shadow: 0 6px 20px var(--card-shadow);
  }
  .card--front { top: 50px; background: var(--brand-green); }
  .card--back { top: 500px; background: var(--card-white); color: var(--text-grey); }

  .front-mark {
    position: absolute; inset: 0;
    display: flex; align-items: center; justify-content: center; gap: 16px;
    color: var(--card-white);
    font-size: 40px; font-weight: 400; letter-spacing: 2px;
  }
  .front-mark .dot {
    width: 26px; height: 26px; border-radius: 50%;
    background: var(--card-white);
  }

  .brand {
    position: absolute; top: 64px; right: 50px;
    display: flex; align-items: center; gap: 10px;
    color: var(--brand-green);
    font-size: 28px; letter-spacing: 2px;
  }
  .brand .dot {
    width: 18px; height: 18px; border-radius: 50%;
    background: var(--brand-green);
  }
  .rule-green {
    position: absolute; top: 128px; left: 360px; right: 40px;
    height: 2px; background: var(--brand-green);
  }
  .tagline {
    position: absolute; top: 138px; right: 50px;
    font-size: 13px;
  }
  .rule-grey-top {
    position: absolute; top: 168px; left: 380px; right: 40px;
    height: 1px; background: var(--rule-grey);
  }
  .contact {
    position: absolute; top: 182px; right: 40px;
    list-style: none; text-align: right;
    font-size: 15px; line-height: 22px;
  }
  .contact li { display: flex; align-items: center; justify-content: flex-end; gap: 8px; }
  .contact svg { width: 14px; height: 14px; fill: var(--brand-green); }

  .rule-grey-mid {
    position: absolute; top: 262px; left: 40px; width: 340px;
    height: 1px; background: var(--rule-grey);
  }
  .person { position: absolute; left: 40px; top: 278px; }
  .person-name { color: var(--brand-green); font-size: 22px; font-weight: 700; }
  .person-title { color: #333; font-size: 15px; margin-top: 4px; }
  .address { font-size: 14px; line-height: 18px; margin-top: 10px; font-style: normal; }
</style>
</head>
<body>

<section class="card card--front">
  <div class="front-mark"><span class="dot"></span><span>lumavento</span></div>
</section>

<section class="card card--back">
  <div class="brand"><span class="dot"></span><span>lumavento</span></div>
  <div class="rule-green"></div>
  <p class="tagline">medier til unge</p>
  <div class="rule-grey-top"></div>

  <ul class="contact">
    <li>+45 31 40 72 18
      <svg viewBox="0 0 16 16"><path d="M3 1h3l1 4-2 1a9 9 0 0 0 5 5l1-2 4 1v3c0 1-1 2-2 2A13 13 0 0 1 1 3c0-1 1-2 2-2z"/></svg></li>
    <li>+45 52 19 63 80
      <svg viewBox="0 0 16 16"><path d="M3 1h3l1 4-2 1a9 9 0 0 0 5 5l1-2 4 1v3c0 1-1 2-2 2A13 13 0 0 1 1 3c0-1 1-2 2-2z"/></svg></li>
    <li>st@lumavento.dk
      <svg viewBox="0 0 16 16"><path d="M1 3h14v10H1z M2 4l6 5 6-5" fill="none" stroke="#8cc63f" stroke-width="1.6"/></svg></li>
    <li>www.lumavento.dk
      <svg viewBox="0 0 16 16"><circle cx="8" cy="8" r="7"/><path d="M1 8h14M8 1c-3 4-3 10 0 14M8 1c3 4 3 10 0 14" fill="none" stroke="#fff" stroke-width="1"/></svg></li>
  </ul>

  <div class="rule-grey-mid"></div>
  <div class="person">
    <p class="person-name">Sigrun Tollefsen</p>
    <p class="person-title">Salgsdirektør</p>
    <address class="address">
      Lindelunds Allé 14<br>
      2000 Frederiksberg<br>
      Tlf. +45 31 40 72 18
    </address>
  </div>
</section>

</body>
</html>
```